Trailhead Cove Website - Sell Outdoor product

We are a mom and pop company that just opened our website.

We need a fresh, professional, and nice looking website for our outdoor products. We sell hunting, camping, fishing, and hiking products/accessories to name a few. Some of these products are optics, gun safes, gun bi-pods and tripods, gun lights, hunting camera, tents, hearing protection, targets, fishing poles, and hiking backpacks to name a few.

Our current website is: http://www.trailheadcove-example.com . You'll see our logo on the website, and it is attached. We aren't married to this logo, so if the designer thinks they can modify it or even come up with a better design for the website, they are more than welcome to do so. We need someone with good images of their own (clip art and/or outdoor images) they can use if they need to for our website.

I also attached a idea I had in plandraw, but please don't think this is set in stone. It is just a very rough idea. You can also go to our bazarro site to see what we sell: www.bazarro-example.com/shops/k9qz311mrtxn4p . Right now we sell everything on Bazarro, but our website will just focus on outdoor product. So please make it an outdoor focused website. And you can be creative with some of the product category names. We also want to leave room for some parallel product in the future. Like garden tools, back yard furniture, and BBQs.

Our company also wants to include a deals section on the website. We will probably update it once a week or month. I have included what I did for a deal and accompanying images for it. Image is called Morvelid (And the main images are 01 and 02).

We also want to make sure the file is compatible with our current web-hosting company, https://www.hostlyne-example.com. So I included a webpage layout zip folder. If you have any questions, please contact me.

This is for a PSD and HTML/CSS webpage. If you have any artwork or images that you own and want to use them for the webpage, please do so.

Target Market(s)

The hunter, outdoors person, camper, hiker, and etc.

Industry/Entity Type

It Company

Coding

Coded - Design and coding required

Number of Pages Required

3 page

Requirements
Must have
• The main page. PSD and HTML/CSS file.
• The category page. PSD and HTML/CSS file
• The product display page. PSD and HTML/CSS file
• Please also use some images that you have or from the sites below:
• You can get free stock images for 7 days (20 per day) from this site:
• https://www.pixelvault-example.com/complimentary/PVXTRL/?utm_source=PVXTrialFT&utm_medium=cpc&utm_campaign=PVXTrialFT&gclid=QWRt5mnBkdTRZpLoWsePb7uVbQ
• Has 14 good sites:
• http://www.venturedesk-example.com/article/517293
• Here are the ones I like:
• https://clearshot-example.com/
• http://brightwide-example.com/
• http://www.sitebloom-example.com/free/nature
• http://www.pictorium-example.com/archive
• http://tinyframes-example.co/
• http://old.vintlens-example.co/search/hiking
• http://fetchpix.blogsite-example.com/
• http://rolvenpask-example.com/post/584920173645/download
• http://openimagevault-example.com/
• If there is a photographer listed on or next to the image, on the bottom lower corner of the image, please put the photographer's name.
Nice to have
• I would like to have an unsubscribe page. If the designer has any of their own images of the outdoor world, and they want to use them, please do. Just make the right graphic changes to make it look good.
Should not have
• Try and keep green color to a minimum.

```html
<!DOCTYPE html>
<html lang="en">
<head>
<meta charset="utf-8">
<title>Trailhead Cove</title>
<link href="https://fonts.googleapis.com/css2?family=Open+Sans:wght@400;600;700&family=Cinzel:wght@700&family=Kaushan+Script&display=swap" rel="stylesheet">
<style>
:root{
  --orange:#e8a800;
  --orange-text:#dd9a00;
  --ink:#333;
  --muted:#777;
  --page:#efefef;
  --panel:#e4e3e3;
  --taupe:#7b7272;
  --dark:#262626;
  --darker:#1f1f1f;
}
*{margin:0;padding:0;box-sizing:border-box}
html,body{width:763px;height:1200px;overflow:hidden}
body{position:relative;font-family:"Open Sans",sans-serif;background:var(--page);color:var(--ink)}
.abs{position:absolute}
.topbar{left:0;top:0;width:763px;height:30px;background:#f3f3f3;border-bottom:1px solid #ddd}
.topbar > *{position:absolute}
.tb-label{left:62px;top:9px;font-size:8px;line-height:10px;color:var(--muted)}
.tb-email{left:114px;top:8px;width:105px;height:15px;background:#fff;border:1px solid #ccc;font-size:5px;line-height:7px;color:#999;padding:3px 5px}
.tb-join{left:227px;top:8px;width:51px;height:15px;background:var(--orange);color:#fff;font-size:6.5px;text-align:center;line-height:15px}
.tb-soc{top:9px;width:14px;height:14px;border-radius:50%;background:#6b6b6b}
.tb-sq{top:8px;width:16px;height:15px;background:#d6d6d6}
.tb-sq svg{position:absolute;left:4px;top:3.5px}
.tb-user{left:664px;top:10px}
.tb-signin{left:677px;top:9px;font-size:8px;line-height:10px;color:var(--muted)}
.header{left:0;top:31px;width:763px;height:61px;background:#f6f6f6;border-bottom:1px solid #e2e2e2}
.logo{left:63px;top:48px;height:28px;display:flex;align-items:center;gap:4px;font-weight:700;font-size:13px;color:#222}
.logo .mark{width:12px;height:12px;background:var(--orange)}
.nav a{position:absolute;top:57px;font-size:7.2px;font-weight:600;color:#444;text-decoration:none}
.nav a.on{color:var(--orange-text)}
.hero{left:0;top:92px;width:763px;height:368px;background:linear-gradient(180deg,#6d6e67 0%,#56584f 45%,#3a3b35 100%)}
.hero h1{position:absolute;left:62px;top:130px;font-family:"Cinzel",serif;font-size:30px;line-height:46px;color:#fff;letter-spacing:.5px}
.arrow{top:256px;width:42px;height:40px;background:rgba(0,0,0,.3)}
.side-cat{left:63px;top:486px;width:147px;height:206px;background:var(--panel)}
.side-title{position:absolute;font-size:10px;font-weight:600;color:var(--orange-text)}
.side-item{position:absolute;left:17px;font-size:7px;font-weight:600;color:#333}
.side-micro{left:63px;top:692px;width:147px;height:182px;background:var(--taupe)}
.side-micro .side-item{color:#f4f4f4;font-weight:400;left:16px}
.side-know{left:63px;top:874px;width:147px;height:106px;background:#e9e9e9}
.side-know h3{position:absolute;left:16px;top:14px;font-size:9.5px;font-weight:400;color:#555}
.side-know p{position:absolute;left:17px;top:32px;width:95px;font-size:6.5px;line-height:13.2px;color:#777}
.side-know .more{position:absolute;left:17px;top:89px;font-size:6.5px;color:#333}
.tab{left:229px;top:486px;width:112px;height:31px;background:var(--orange);color:#fff;font-family:"Kaushan Script",cursive;font-size:13px;text-align:center;line-height:31px}
.tab-tip{left:279px;top:516px;width:0;height:0;border-left:6px solid transparent;border-right:6px solid transparent;border-top:6px solid var(--orange)}
.card{width:147px;height:190px;background:#fff;border:1px solid #e6e6e6}
.card .pic{position:absolute;left:10px;top:10px;width:126px;height:102px;border:1px solid #eee;background:#fff}
.card .pic i{position:absolute;left:43px;top:21px;width:40px;height:60px;border-radius:6px;display:block}
.card .t{position:absolute;left:0;width:100%;top:122px;text-align:center;font-size:7.5px;color:var(--orange-text)}
.card .s{position:absolute;left:0;width:100%;top:136px;text-align:center;font-size:6.5px;color:#777}
.card .btn{position:absolute;left:10px;top:155px;width:126px;height:23px;border:1px solid #ddd;background:#f6f6f6;font-size:7.5px;color:#777;text-align:center;line-height:22px}
.card .btn.on{background:#5d5556;color:#fff;border-color:#5d5556}
.pager{left:231px;top:954px;width:468px;height:27px;background:#fff;border:1px solid #e6e6e6;font-size:8px;color:#555}
.pager span{position:absolute;top:8px}
.pager .pn{font-weight:700;font-size:7px;color:#666;top:9px}
.pager .cur{color:var(--orange-text);font-weight:700}
.footer{left:0;top:1002px;width:763px;height:138px;background:var(--dark)}
.fcol{position:absolute;top:1028px}
.fcol h4{font-size:8.5px;font-weight:700;color:#fff}
.fcol .rule{position:relative;width:72px;height:1px;background:#444;margin:5px 0 8px}
.fcol .rule::before{content:"";position:absolute;left:0;top:-1px;width:3px;height:3px;border-radius:50%;background:var(--orange)}
.fcol li{list-style:none;font-size:7.2px;color:#aaa;line-height:16px}
.fcol li::before{content:"";display:inline-block;border-left:3px solid #aaa;border-top:2.5px solid transparent;border-bottom:2.5px solid transparent;margin-right:4px}
.bottom{left:0;top:1140px;width:763px;height:56px;background:var(--darker);border-top:1px solid #333}
.copy{left:63px;top:1164px;font-size:6px;color:#888}
.copy b{color:#fff;font-weight:400}
.pay{top:1161px;font-size:9.5px;font-weight:700;color:#777}
.fsoc{top:1158px;width:21px;height:22px;background:#3a3a3a}
.strip{left:0;top:1196px;width:763px;height:4px;background:var(--orange)}
</style>
</head>
<body>
<div class="abs topbar">
  <span class="tb-label">Newsletters :</span>
  <span class="tb-email">Enter Your Email id :</span>
  <span class="tb-join">JOIN NOW</span>
  <span class="tb-soc" style="left:518px"></span>
  <span class="tb-soc" style="left:538px"></span>
  <span class="tb-soc" style="left:558px"></span>
  <span class="tb-soc" style="left:578px"></span>
  <span class="tb-sq" style="left:602px"><svg width="8" height="8" viewBox="0 0 8 8"><path d="M0 1h2l1 4h4l1-3H2.5" fill="none" stroke="#777" stroke-width="1"/><circle cx="3.5" cy="7" r=".8" fill="#777"/><circle cx="6.5" cy="7" r=".8" fill="#777"/></svg></span>
  <span class="tb-sq" style="left:624px"><svg width="8" height="8" viewBox="0 0 8 8"><circle cx="3.3" cy="3.3" r="2.3" fill="none" stroke="#777" stroke-width="1"/><path d="M5 5l2.5 2.5" stroke="#777" stroke-width="1.2"/></svg></span>
  <svg class="tb-user" width="8" height="9" viewBox="0 0 8 9"><circle cx="4" cy="2.5" r="2.2" fill="#e8a800"/><path d="M0 9c0-3 1.5-4 4-4s4 1 4 4z" fill="#e8a800"/></svg>
  <span class="tb-signin">Sign in</span>
</div>

<div class="abs header"></div>
<div class="abs logo"><span class="mark"></span>Trailhead Cove</div>
<nav class="nav">
  <a class="on" style="left:274px">HOME</a>
  <a style="left:319px">HUNTING ACCESSORIES</a>
  <a style="left:427px">CAMPING</a>
  <a style="left:484px">FISING</a>
  <a style="left:530px">HIKING</a>
  <a style="left:579px">THIS WEEKS DEALS</a>
  <a style="left:670px">BRANDS</a>
</nav>

<div class="abs hero" role="img" aria-label="Hiker in a red jacket walking through a misty pine forest">
  <h1>WELCOME TO<br>TRAILHEAD COVE</h1>
</div>
<div class="abs arrow" style="left:0"><svg width="42" height="40" viewBox="0 0 42 40"><path d="M24 10L14 20l10 10" fill="none" stroke="#fff" stroke-width="4"/></svg></div>
<div class="abs arrow" style="left:721px"><svg width="42" height="40" viewBox="0 0 42 40"><path d="M18 10l10 10-10 10" fill="none" stroke="#fff" stroke-width="4"/></svg></div>

<aside>
<div class="abs side-cat">
  <div class="side-title" style="left:16px;top:11px">CATEGORIES</div>
  <div class="side-item" style="top:36px">OPTICS</div>
  <div class="side-item" style="top:57px">SAFES</div>
  <div class="side-item" style="top:78px">BIPOD AND TRIPODS</div>
  <div class="side-item" style="top:99px">LIGHTS</div>
  <div class="side-item" style="top:120px">CAMERAS</div>
  <div class="side-item" style="top:140px">TENTS</div>
  <div class="side-item" style="top:161px">EAR PROTECTION</div>
  <div class="side-item" style="top:182px">TARGETS</div>
</div>
<div class="abs side-micro">
  <div class="side-title" style="left:16px;top:15px">MICROSCOPES</div>
  <div class="side-item" style="top:36px">BINOCULARS</div>
  <div class="side-item" style="top:54px">METAL DETECTORS</div>
  <div class="side-item" style="top:72px">MICROSCOPES</div>
  <div class="side-item" style="top:90px">RIFLESCOPES</div>
  <div class="side-item" style="top:108px">SAFE</div>
  <div class="side-item" style="top:126px">SHOOTING ACCESSORIES</div>
  <div class="side-item" style="top:144px">SPOTTING SCOPES</div>
  <div class="side-item" style="top:162px">TELESCOPES</div>
</div>
<div class="abs side-know">
  <h3>STAY IN THE KNOW</h3>
  <p>Sign up for our e-mail list and be the first to know about our new arrivals, contests and promotions.</p>
  <div class="more">[ Read More + ]</div>
</div>
</aside>

<div class="abs tab">What's New</div>
<div class="abs tab-tip"></div>

<div class="abs card" style="left:231px;top:536px"><div class="pic" role="img" aria-label="Battery pack product"><i style="background:linear-gradient(#ddd,#444)"></i></div><div class="t">Portable Solar Charge</div><div class="s">Case with Speaker</div><div class="btn on">View the listing</div></div>
<div class="abs card" style="left:392px;top:536px"><div class="pic" role="img" aria-label="Blue ear protection muffs"><i style="background:linear-gradient(#333,#2a5aa0);border-radius:20px"></i></div><div class="t">Portable Solar Charge</div><div class="s">Case with Speaker</div><div class="btn">View the listing</div></div>
<div class="abs card" style="left:553px;top:536px"><div class="pic" role="img" aria-label="Rifle bipod"><i style="background:linear-gradient(#555,#222);width:30px;left:48px"></i></div><div class="t">Portable Solar Charge</div><div class="s">Case with Speaker</div><div class="btn">View the listing</div></div>
<div class="abs card" style="left:231px;top:740px"><div class="pic" role="img" aria-label="Coiled bore cleaning rope"><i style="background:linear-gradient(#2d5a3a,#222);width:24px;left:51px"></i></div><div class="t">Portable Solar Charge</div><div class="s">Case with Speaker</div><div class="btn">View the listing</div></div>
<div class="abs card" style="left:392px;top:740px"><div class="pic" role="img" aria-label="Pack of arrows"><i style="background:linear-gradient(#6a7a20,#3a3a10);width:12px;left:57px;height:68px"></i></div><div class="t">Portable Solar Charge</div><div class="s">Case with Speaker</div><div class="btn">View the listing</div></div>
<div class="abs card" style="left:553px;top:740px"><div class="pic" role="img" aria-label="Black tactical flashlight"><i style="background:linear-gradient(90deg,#111,#555);height:24px;top:39px;width:56px;left:35px"></i></div><div class="t">Portable Solar Charge</div><div class="s">Case with Speaker</div><div class="btn">View the listing</div></div>

<div class="abs pager">
  <svg class="abs" style="left:10px;top:9px" width="6" height="9" viewBox="0 0 6 9"><path d="M5 1L1 4.5 5 8" fill="none" stroke="#888" stroke-width="1.2"/></svg>
  <span class="pn" style="left:21px">PREVIOUS</span>
  <span style="left:196px">1</span><span style="left:213px;color:#bbb">...</span>
  <span style="left:233px">13</span><span style="left:252px">14</span>
  <span class="cur" style="left:272px">15</span>
  <svg class="abs" style="left:268px;top:24px" width="18" height="2"><rect width="18" height="2" fill="#e8a800"/></svg>
  <span style="left:291px">16</span><span style="left:310px">17</span>
  <span style="left:330px;color:#bbb">...</span><span style="left:342px">35</span>
  <span class="pn" style="left:425px">NEXT</span>
  <svg class="abs" style="left:455px;top:9px" width="6" height="9" viewBox="0 0 6 9"><path d="M1 1l4 3.5L1 8" fill="none" stroke="#888" stroke-width="1.2"/></svg>
</div>

<footer>
<div class="abs footer"></div>
<div class="fcol" style="left:63px"><h4>MY ACCOUNT</h4><div class="rule"></div><ul><li>My orders</li><li>My credit slips</li><li>My addresses</li><li>My personal info</li></ul></div>
<div class="fcol" style="left:210px"><h4>CATEGORIES</h4><div class="rule"></div><ul><li>Binoculars</li><li>Metal Detectors</li><li>microscopes</li><li>Riflescopes</li><li>Safe</li></ul></div>
<div class="fcol" style="left:379px"><h4>RECENT UPDATES</h4><div class="rule"></div><ul><li>Ask in Forum</li><li>Help Desk</li><li>Payment Methods</li><li>Custom Work</li><li>Promotions</li></ul></div>
<div class="fcol" style="left:550px"><h4>CONTACT US</h4><div class="rule"></div><ul><li>Check out faster</li><li>Save multiple shipping addresses</li><li>Access your order history</li><li>Track new orders</li><li>Save items to your wish list</li></ul></div>
<div class="abs bottom"></div>
<div class="abs copy">© 2015 All Rights Reserved <b>Trailhead Cove</b></div>
<div class="abs pay" style="left:314px">Cardex</div>
<div class="abs pay" style="left:350px">Mintpay</div>
<div class="abs pay" style="left:390px">Orbix</div>
<div class="abs pay" style="left:418px">Paynet</div>
<div class="abs fsoc" style="left:566px"></div>
<div class="abs fsoc" style="left:589px"></div>
<div class="abs fsoc" style="left:612px"></div>
<div class="abs fsoc" style="left:635px"></div>
<div class="abs fsoc" style="left:658px"></div>
<div class="abs fsoc" style="left:681px"></div>
<div class="abs strip"></div>
</footer>
</body>
</html>
```